Business card design for a dynamic IT consulting company

We need a business card design for a young firm, specialized in the Telecommunications/Consulting industry. The name of the company is Quindor and Partners Business Consulting Ltd. (Short name: Quindor and Partnes)
Quindor = solve read reverse, so we aim to be uncomplicated and solution-oriented. The small pipe in our logo is also related to the word solve. So we need a new business card design, which is simple, eye catching and something non traditional (I would probably prefer a square shaped design rather than a rectangle, but open for suggestions). Attached our logo.

Target Market(s)

Usually our customers are Tier1 Telecoms providers (Q-Netra, Palorix, etc) and their executives.

Industry/Entity Type

Business

Contact Information for Business Card

Name: Bence Tolnavari
Email: b.tolnavari@quindor.hu
Web: www.quindor.hu
Mobile: +36 30 518 2769
Title: Managing Director

Optional:
Company name: Quindor and Partners Ltd.
Address: 1087 Budapest, Tolvenka str. 28/C, Hungary

Font styles to use
Other font styles liked:
• helveticaneue_medium, Prime Regular are used now.

Colors

Designer to choose colors to be used in the design.

Requirements
Must have
• I would like to have a 2 sided design.
Nice to have
• I thought if we make the logo a bit bigger (without the company name), that could go to the back with the company name below. I though, if the pipe in the logo is somehow touchable on the business card, would be nice and unique.

```html
<!DOCTYPE html>
<html lang="en">
<head>
<meta charset="utf-8">
<title>Quindor and Partners – Business Card</title>
<link rel="stylesheet" href="https://fonts.googleapis.com/css2?family=Exo+2:wght@400;500;600&display=swap">
<style>
  :root {
    --page-bg: #ebe8e4;
    --card-light: #ffffff;
    --card-dark: #1d1d1f;
    --magenta: #b12f93;
    --blue: #1b9ad8;
    --ink: #3a3a3c;
    --ink-soft: #6b6b6e;
    --paper-text: #f4f4f4;
  }
  * { box-sizing: border-box; margin: 0; padding: 0; }
  html, body {
    width: 1200px; height: 780px; overflow: hidden;
    background: var(--page-bg);
    font-family: "Exo 2", "Helvetica Neue", Arial, sans-serif;
  }
  .sheet {
    position: relative; width: 1200px; height: 780px;
    display: flex; align-items: center; justify-content: center; gap: 40px;
  }
  .card {
    position: relative; width: 540px; height: 309px; overflow: hidden;
    box-shadow: 0 10px 28px rgba(0,0,0,.18);
  }
  .accent-band {
    position: absolute; left: 0; right: 0; bottom: 0; height: 11px;
    background: linear-gradient(90deg, var(--magenta) 0 50%, var(--blue) 50% 100%);
  }

  /* Front side */
  .card--front { background: var(--card-light); }
  .front-brand {
    position: absolute; top: 105px; left: 0; right: 0;
    display: flex; align-items: center; justify-content: center; gap: 12px;
  }
  .brand-square { width: 14px; height: 14px; background: var(--blue); }
  .brand-name {
    font-weight: 500; font-size: 36px; letter-spacing: .5px; color: var(--ink);
  }
  .front-web {
    position: absolute; top: 190px; left: 0; right: 0; text-align: center;
    font-size: 13px; letter-spacing: 3px; color: var(--ink-soft);
  }

  /* Back side */
  .card--back { background: var(--card-dark); color: var(--paper-text); }
  .back-brand {
    position: absolute; top: 34px; right: 40px;
    display: flex; align-items: center; gap: 10px;
  }
  .back-brand .brand-name { color: var(--paper-text); font-size: 30px; }
  .person { position: absolute; top: 112px; left: 36px; }
  .person-name { font-weight: 600; font-size: 19px; letter-spacing: .3px; }
  .person-title { font-size: 13px; color: var(--magenta); margin-top: 1px; }
  .divider {
    position: absolute; top: 160px; left: 36px; right: 36px; height: 1px;
    background: linear-gradient(90deg, var(--magenta) 0 45%, var(--blue) 45% 100%);
  }
  .contacts { position: absolute; top: 172px; left: 36px; list-style: none; }
  .contacts li {
    display: flex; align-items: center; gap: 8px;
    font-size: 12.5px; line-height: 19px;
  }
  .contacts svg { width: 11px; height: 11px; flex: none; }
  .company {
    position: absolute; right: 36px; bottom: 34px; text-align: left;
  }
  .company-name { font-weight: 600; font-size: 15px; letter-spacing: .4px; }
  .company-address { font-size: 12.5px; line-height: 17px; margin-top: 2px; }
</style>
</head>
<body>
<main class="sheet">

  <section class="card card--front" aria-label="Card front">
    <div class="front-brand">
      <span class="brand-square"></span>
      <span class="brand-name">Quindor &amp; Partners</span>
    </div>
    <p class="front-web">www.quindor.hu</p>
    <div class="accent-band"></div>
  </section>

  <section class="card card--back" aria-label="Card back">
    <div class="back-brand">
      <span class="brand-square"></span>
      <span class="brand-name">Quindor &amp; Partners</span>
    </div>

    <div class="person">
      <p class="person-name">Bence Tolnavari</p>
      <p class="person-title">Managing Director</p>
    </div>
    <div class="divider"></div>

    <ul class="contacts">
      <li>
        <svg viewBox="0 0 12 12" aria-hidden="true"><rect x="3" y="0.5" width="6" height="11" rx="1" fill="none" stroke="var(--magenta)" stroke-width="1.2"/></svg>
        +36 30 518 2769
      </li>
      <li>
        <svg viewBox="0 0 12 12" aria-hidden="true"><rect x="0.5" y="2" width="11" height="8" fill="#fff"/><path d="M0.5 2 L6 6.5 L11.5 2" fill="none" stroke="var(--card-dark)" stroke-width="1"/></svg>
        b.tolnavari@quindor.hu
      </li>
      <li>
        <svg viewBox="0 0 12 12" aria-hidden="true"><circle cx="6" cy="6" r="5.3" fill="none" stroke="var(--blue)" stroke-width="1.2"/><ellipse cx="6" cy="6" rx="2.3" ry="5.3" fill="none" stroke="var(--blue)" stroke-width="1"/><line x1="0.7" y1="6" x2="11.3" y2="6" stroke="var(--blue)" stroke-width="1"/></svg>
        www.quindor.hu
      </li>
    </ul>

    <div class="company">
      <p class="company-name">Quindor and Partners Ltd.</p>
      <p class="company-address">1087 Budapest<br>Tolvenka str. 28/C, Hungary</p>
    </div>
    <div class="accent-band"></div>
  </section>

</main>
</body>
</html>
```